Business Card Design Project

We need a business card for a new technology services company. We develop software and implement software packages for our business customers and although we will begin with just one or two service offerings, our service offerings will expand over time. Our name comes from the an author, KL Barrow, and his "idea" was that opportunity should be based on ability and achievement, not on social status.

We would like to see a design that is standard in its size and shape, but stands apart in its dramatic color contrasts. The card should not use too many colors - the colors used in the background should highlight the brilliant blues of the logo (see attachment) to dramatic effect. The background should not be white.

If necessary, you can change the color of the words "KL Barrow", but not the word "Idea".

Card size should be U.S. standard 2 inches by 3.5 inches and provide for 1/8 inch bleed area on each side.

We need a design for both sides of the business card, one side communicating the company logo and contact information, the other side being purely graphical, incorporating the logo but no other information.

Contact Information Required:
Kate Brook
KateBrook@klbarrowvista.com
614-387-2259

Target Market(s)

Business executives

Industry/Entity Type

Software

Requirements
Must have
• It must have the full company logo on one side, and at least the graphic element of the logo on the other. Either that or the full logo on both.
Nice to have
• It would be nice to have a design that could work without needing two different textures. For example, it would be nice if the entire card could be shiny, not just parts of the card.

It would also be nice if texture is something we could add later.
Should not have
• The card should not use the color green.

```html
<!DOCTYPE html>
<html lang="en">
<head>
<meta charset="utf-8">
<title>Corvane Systems Business Card</title>
<link rel="stylesheet" href="https://fonts.googleapis.com/css2?family=Open+Sans:wght@400;600&display=swap">
<style>
  :root {
    --backdrop: #404040;
    --sheet: #ffffff;
    --band-deep: #0077b6;
    --band-bright: #00b0f0;
    --card-light: #ffffff;
    --card-sky: #98bfe6;
    --card-sky-deep: #74aad6;
    --brand-blue: #0a9ad8;
    --ink-dark: #1e1e1e;
    --ink-mid: #555a60;
    --ink-soft: #9a9a9a;
  }
  * { margin: 0; padding: 0; box-sizing: border-box; }
  html, body {
    width: 1200px; height: 900px; overflow: hidden;
    background: var(--backdrop);
    font-family: "Open Sans", sans-serif;
  }
  .board { position: relative; width: 1200px; height: 900px; }
  .sheet {
    position: absolute; left: 212px; top: 0; width: 776px; height: 900px;
    background: var(--sheet);
  }
  .title-band {
    position: absolute; left: 212px; top: 48px; width: 288px; height: 61px;
    background: linear-gradient(90deg, var(--band-deep), var(--band-bright));
    color: #fff; font-size: 13px; letter-spacing: 0.3px;
    padding: 19px 0 0 58px;
  }
  .card {
    position: absolute; top: 290px; width: 561px; height: 320px;
    box-shadow: 2px 3px 6px rgba(0,0,0,0.55);
  }
  .card--front {
    left: 20px;
    background: radial-gradient(ellipse 320px 200px at 280px 180px, var(--card-light) 0%, #e6f0fa 35%, var(--card-sky) 100%);
  }
  .card--back {
    left: 610px;
    background: radial-gradient(ellipse 300px 220px at 110px 150px, var(--card-light) 0%, #d8e8f6 35%, var(--card-sky-deep) 100%);
  }
  .brand-name {
    position: absolute; left: 180px; top: 172px;
    font-size: 20px; font-weight: 600; color: var(--brand-blue);
    letter-spacing: -0.3px; white-space: nowrap;
  }
  .brand-dot {
    position: absolute; left: 345px; top: 140px; width: 34px; height: 34px;
    border-radius: 50%; background: var(--brand-blue);
  }
  .brand-dot--large {
    left: 40px; top: 100px; width: 130px; height: 130px;
  }
  .contact {
    position: absolute; left: 279px; top: 121px;
    padding-left: 26px; border-left: 2px solid var(--brand-blue);
    font-size: 12.5px; letter-spacing: 0.3px; line-height: 24px;
    text-transform: uppercase; color: var(--ink-mid); white-space: nowrap;
  }
  .contact .contact-name { color: var(--ink-dark); }
  .sheet-footer {
    position: absolute; left: 0; top: 820px; width: 1200px;
    text-align: center; font-size: 11px; color: var(--ink-soft);
  }
  .sheet-footer .divider { margin: 0 10px; }
  .sheet-footer .footer-email { color: var(--ink-dark); font-size: 12px; }
  .sheet-footer .footer-email .accent { color: var(--brand-blue); }
</style>
</head>
<body>
<main class="board">
  <div class="sheet"></div>
  <header class="title-band">Corvane Systems Services</header>

  <section class="card card--front" aria-label="Card front">
    <span class="brand-name">Corvane Systems</span>
    <span class="brand-dot"></span>
  </section>

  <section class="card card--back" aria-label="Card back">
    <span class="brand-dot brand-dot--large"></span>
    <div class="contact">
      <p class="contact-name">Kate Brook</p>
      <p>KateBrook@klbarrowvista.com</p>
      <p>614-387-2259</p>
    </div>
  </section>

  <footer class="sheet-footer">
    New technology services company&nbsp; 614-387-2259<span class="divider">|</span><span class="footer-email">katebrook<span class="accent">@klbarrowvista</span>.com</span>
  </footer>
</main>
</body>
</html>
```